Book Cover for a book on Quiet Ventures

I am self-publishing my book on Brindlecart and need a book cover made. Below are the details. See attached templates for size we need to use. I also attached a previous cover we had made that I liked. The problem with it was they were two boys helping each other but the book is about women. I'm open to your ideas on the cover though, but I wanted to show you a style I liked as an idea.
Front of Cover
Book Title: Quiet Ventures
Book Subtitle: Unvarnished Notes of a Woman Founder
Author Name: Lorna T. Pelham
Add on the Spine of Cover: Quiet Ventures and Lorna T. Pelham
Back of the Cover Text:
Quiet Ventures: Unvarnished Notes of a Woman Founder is an honest account of a business owner’s experience attempting to navigate the start-up community while also pursuing spiritual growth. Author Lorna Pelham defines a spiritual entrepreneur as “someone who runs an enterprise with the purpose of growing love rather than material gain.” This book discusses the three dimensions of Quiet Ventures:
1. The business is an integral part of the founder’s spiritual journey.
2. Employees working for the spiritual enterprise, whether they know it or not, encounter this company because it's part of their spiritual path.
3. The business itself has a life force of its own and its purpose is to further the kingdom of heaven on earth.
These three dimensions happen simultaneously and work together to produce the greatest possible result. However, this can feel confusing to a founder juggling these dimensions while also trying to manage and run a business. This is not a formulaic self-help book or roadmap. Rather, it is a compilation of personal reflections that often seem at odds with the traditional world of entrepreneurship.
Below the description add my picture (see attached for my picture)
Bio text:
Lorna Pelham founded Halvex with the vision of ushering in a life-long education system that shifts away from standardization to one that empowers people to live their purpose. In college, Lorna interned for Open Meadow, a women’s empowerment initiative where she recognized her passion for helping people find their voice. Lorna's 20-year journey has come full circle to empowering other female CEOs who are pursuing the path of Quiet Ventures.
NOTE: Please note that Brindlecart puts a bar code on the bottom right of the back cover as is noted on the attached template.
Size template is attached to the brief, here are the sizes typed out:
# Description Width (in) Height (in)
1 Full Cover 12.79 9.25
2 Front Cover 6 9
3 Safe Area 5.875 8.75
4 Bleed 0.125 0.125
5 Margin 0.125 0.125
6 Spine 0.54 9
7 Spine Safe Area 0.415 8.75
8 Spine Margin 0.062 0.062
9 Barcode Margin 0.25 0.25
Pre-publication checklist
BRINDLECART TIPS for the final cover:
1. Save as a PDF. Your cover must be a single PDF that includes the back cover, spine, and front cover as one image.
2. Flatten all transparencies. These can cause the file to print with missing or distorted content. Consult your software's documentation to learn how.
3. Embed your fonts. Consult your software's documentation to learn how.
4. Remove crop marks, color bars, template text. Crop marks are lines showing where pages should be trimmed. Color bars are strips with a series of patches used to ensure color balance during printing. Also, remove any template text, PDF creation guides, or software references.
5. Ensure your cover image meets the minimum resolution of 300 DPI (dots per inch).
6. Optimize PDFs. Optimization is useful to reduce your file size, allowing for higher performance when transferring, uploading, viewing, and printing the files.
7. Remove file security. Locked or encrypted files will fail review.
Target Market(s)
Women who want to be CEOs or are currently CEOs of companies.
Industry/Entity Type
Entrepreneurship, business, spirituality
Requirements
Must have
- Just the text on the description. A very welcoming feel.
Nice to have
- I like the idea of having a sunrise/sunset in the image somehow like in the example I attached to the brief, but again I'm open.
Should not have
- Please don't put any yoga or meditation poses or hands outstretched. I have a lot of interesting ones that look like my example so if you are going to submit after Saturday 10/29, please only do so if you have a new idea! Thanks!

```html
<!DOCTYPE html>
<html lang="en">
<head>
<meta charset="utf-8">
<title>Quiet Ventures — Full Cover</title>
<link rel="stylesheet" href="https://fonts.googleapis.com/css2?family=Playfair+Display:wght@400;700&display=swap">
<style>
  :root {
    --purple: #63449a;
    --spine: #5e4193;
    --gold: #f9c513;
    --white: #ffffff;
    --text: #f3eefa;
    --stage: #2b2b30;
    --photo-light: #e9eaec;
    --photo-mid: #b9b8bd;
    --photo-dark: #54505c;
  }
  * { box-sizing: border-box; margin: 0; padding: 0; }
  html, body { width: 806px; height: 1200px; overflow: hidden; }
  body {
    background: var(--stage);
    position: relative;
    font-family: "Playfair Display", Georgia, serif;
  }
  .cover-wrap {
    position: absolute;
    left: 18px;
    top: 324px;
    width: 1380px;
    height: 988px;
    transform: scale(0.558);
    transform-origin: top left;
    background: var(--purple);
    border-top: 8px solid var(--gold);
    border-bottom: 8px solid var(--gold);
    overflow: hidden;
  }

  /* Back cover */
  .back-cover { position: absolute; left: 0; top: 0; width: 658px; height: 100%; }
  .title-block {
    position: absolute; left: 0; width: 100%; text-align: center; line-height: 1;
    font-weight: 400;
  }
  .back-cover .title-block { top: 36px; }
  .title-main { color: var(--gold); font-size: 80px; font-weight: 400; letter-spacing: 1px; display: block; }
  .title-sub { color: var(--white); font-size: 42px; font-weight: 400; letter-spacing: 1px; display: block; margin-top: 4px; }

  .blurb {
    position: absolute; left: 50px; top: 180px; width: 559px;
    color: var(--text); font-size: 14.6px; line-height: 16.6px; text-align: justify;
  }
  .blurb p { margin-bottom: 16px; }
  .blurb ol { margin: 0 0 16px 24px; padding: 0; }
  .blurb li { font-weight: 700; padding-left: 2px; }

  .author-rule {
    position: absolute; left: 93px; top: 581px; width: 473px; height: 2px; background: var(--gold);
  }
  .author-photo {
    position: absolute; left: 245px; top: 498px; width: 170px; height: 170px;
    border-radius: 50%; border: 3px solid var(--gold);
    background: radial-gradient(circle at 50% 40%, #c9a58e 0%, #6e4a36 45%, #6f8f4f 75%, #e24a6a 100%);
  }
  .bio {
    position: absolute; left: 75px; top: 688px; width: 510px;
    color: var(--text); font-size: 14.6px; line-height: 19.6px; text-align: center;
  }
  .bio strong { font-weight: 700; }

  /* Spine */
  .spine {
    position: absolute; left: 658px; top: 0; width: 63px; height: 100%;
    background: var(--spine);
    border-left: 1px solid #7a5fae;
    border-right: 2px solid #1d1530;
  }
  .spine-title, .spine-author {
    position: absolute; left: 50%; writing-mode: vertical-rl; transform: translateX(-50%);
    white-space: nowrap; font-weight: 400;
  }
  .spine-title { top: 40px; color: var(--text); font-size: 30px; letter-spacing: 2px; }
  .spine-author { top: 670px; color: var(--gold); font-size: 34px; }

  /* Front cover */
  .front-cover { position: absolute; left: 721px; top: 0; width: 659px; height: 100%; }
  .front-photo {
    position: absolute; left: 0; top: 0; width: 100%; height: 535px;
    background:
      linear-gradient(180deg, rgba(99,68,154,0) 75%, var(--purple) 100%),
      linear-gradient(90deg, var(--photo-light) 0%, var(--photo-mid) 30%, var(--photo-dark) 55%, var(--photo-mid) 75%, var(--photo-light) 100%);
  }
  .front-cover .title-block { top: 582px; }
  .front-cover .title-main { font-size: 112px; }
  .front-cover .title-sub { font-size: 58px; margin-top: 2px; }
  .subtitle-rule { position: absolute; left: 114px; width: 430px; height: 1px; background: var(--gold); }
  .subtitle-rule.upper { top: 783px; }
  .subtitle-rule.lower { top: 842px; }
  .subtitle {
    position: absolute; left: 0; top: 792px; width: 100%; text-align: center;
    color: var(--white); font-size: 29px; font-weight: 400; line-height: 40px; letter-spacing: 0.3px;
    white-space: nowrap;
  }
  .author-name {
    position: absolute; left: 0; top: 888px; width: 100%; text-align: center;
    color: var(--gold); font-size: 52px; font-weight: 400; line-height: 62px;
  }
</style>
</head>
<body>
  <div class="cover-wrap">
    <section class="back-cover">
      <h2 class="title-block">
        <span class="title-main">QUIET</span>
        <span class="title-sub">VENTURES</span>
      </h2>
      <div class="blurb">
        <p>Quiet Ventures: Unvarnished Notes of a Woman Founder is an honest account of a business owner’s experience attempting to navigate the start-up community while also pursuing spiritual growth. Author Lorna Pelham defines a spiritual entrepreneur as “someone who runs an enterprise with the purpose of growing love rather than material gain.” This book discusses the three dimensions of Quiet Ventures:</p>
        <ol>
          <li>The business is an integral part of the founder’s spiritual journey.</li>
          <li>Employees working for the spiritual enterprise, whether they know it or not, encounter this company because it's part of their spiritual path.</li>
          <li>The business itself has a life force of its own and its purpose is to further the kingdom of heaven on earth.</li>
        </ol>
        <p>These three dimensions happen simultaneously and work together to produce the greatest possible result. However, this can feel confusing to a founder juggling these dimensions while also trying to manage and run a business. This is not a formulaic self-help book or roadmap. Rather, it is a compilation of personal reflections that often seem at odds with the traditional world of entrepreneurship.</p>
      </div>
      <div class="author-rule"></div>
      <div class="author-photo" role="img" aria-label="Portrait photo of the author, smiling, with long brown hair and a pink top, greenery behind"></div>
      <p class="bio"><strong>Lorna Pelham</strong> founded Halvex with the vision of ushering in a life-long education system that shifts away from standardization to one that empowers people to live their purpose. In college, Lorna interned for Open Meadow, a women’s empowerment initiative where she recognized her passion for helping people find their voice. Lorna's 20-year journey has come full circle to empowering other female CEOs who are pursuing the path of Quiet Ventures.</p>
    </section>

    <section class="spine">
      <span class="spine-title">QUIET VENTURES</span>
      <span class="spine-author">Lorna T. Pelham</span>
    </section>

    <section class="front-cover">
      <div class="front-photo" role="img" aria-label="Photo of a businesswoman seated in a tan egg chair with a laptop, in front of tall office windows overlooking a hazy city"></div>
      <h1 class="title-block">
        <span class="title-main">QUIET</span>
        <span class="title-sub">VENTURES</span>
      </h1>
      <div class="subtitle-rule upper"></div>
      <p class="subtitle">Unvarnished Notes of a Woman Founder</p>
      <div class="subtitle-rule lower"></div>
      <p class="author-name">Lorna T. Pelham</p>
    </section>
  </div>
</body>
</html>
```